Veltrane Group Business Card Design

The CEO is looking for a new trendy look for his business card.
You can stay with current branding or come up with something new/creative. It can be 3D, including Medical Office buildings. You can use our logo in a variety of colors. Please include name, title, company name, company website, email address, cell number

Target Market(s)

Real Estate Development and Construction

Industry/Entity Type

Health care real estate

Contact Information for Business Card

Rohesh Kamdar, CEO M-604.781.2249 E-roheshkamdar@veltrane.com Address:4180 Lindqvist Ave, Tampa, FL 33482 www.veltrane.com

Font styles to use
Other font styles liked:
• Be creative

Requirements
Must have
• Creative, trendy look
Nice to have
• Please go to our website to get a feel- www. veltrane.com
Should not have
• small fonts

```html
<!DOCTYPE html>
<html lang="en">
<head>
<meta charset="utf-8">
<title>Veltrane Group Business Card</title>
<link rel="stylesheet" href="https://fonts.googleapis.com/css2?family=Montserrat:wght@400;500;700;800&display=swap">
<style>
  :root {
    --backdrop: #cbc3b1;
    --card-white: #ffffff;
    --card-black: #181818;
    --brand-red: #b01e28;
    --brand-navy: #1c3050;
    --ink: #1f1f1f;
  }
  * { box-sizing: border-box; margin: 0; padding: 0; }
  html, body { width: 1116px; height: 1200px; overflow: hidden; }
  body {
    background: var(--backdrop);
    font-family: "Montserrat", sans-serif;
    position: relative;
  }
  .card {
    position: absolute;
    left: 217px;
    width: 682px;
    height: 391px;
    overflow: hidden;
  }
  .card-front { top: 184px; background: var(--card-white); }
  .card-back { top: 625px; background: var(--card-black); }

  .brand-name {
    position: absolute;
    color: var(--brand-red);
    font-weight: 800;
    letter-spacing: -0.02em;
    line-height: 0.95;
    text-align: right;
  }
  .card-front .brand-name { right: 362px; top: 142px; font-size: 46px; }
  .card-back .brand-name { left: 0; right: 0; top: 92px; font-size: 104px; text-align: center; }

  .divider {
    position: absolute;
    left: 336px; top: 117px;
    width: 2px; height: 154px;
    background: var(--brand-red);
  }
  .contact { position: absolute; left: 360px; top: 115px; right: 20px; }
  .person-name {
    color: var(--brand-red);
    font-weight: 700;
    font-size: 28px;
    letter-spacing: 0.01em;
    line-height: 1.1;
    white-space: nowrap;
  }
  .person-title { color: var(--ink); font-size: 21px; font-weight: 400; margin-top: 4px; }
  .contact-list { list-style: none; margin-top: 14px; }
  .contact-list li {
    display: flex; align-items: center;
    color: var(--ink); font-size: 18px; line-height: 30px;
    white-space: nowrap;
  }
  .contact-list svg { width: 14px; height: 14px; margin-right: 8px; flex: none; }

  .accent-line {
    position: absolute; left: 0; top: 330px;
    width: 100%; height: 4px; background: var(--brand-red);
  }
  .address-band {
    position: absolute; left: 0; top: 337px;
    width: 100%; height: 54px;
    background: var(--brand-navy);
    color: #fff; font-size: 20px;
    text-align: center; line-height: 40px;
  }
</style>
</head>
<body>
  <section class="card card-front">
    <div class="brand-name">Veltrane<br>Group</div>
    <div class="divider"></div>
    <div class="contact">
      <div class="person-name">ROHESH KAMDAR</div>
      <div class="person-title">CEO</div>
      <ul class="contact-list">
        <li>
          <svg viewBox="0 0 14 14" aria-hidden="true"><rect x="3.5" y="1" width="7" height="12" rx="1.2" fill="none" stroke="#b01e28" stroke-width="1.6"/><circle cx="7" cy="10.8" r="0.9" fill="#b01e28"/></svg>
          604.781.2249
        </li>
        <li>
          <svg viewBox="0 0 14 14" aria-hidden="true"><rect x="1" y="3" width="12" height="8.5" fill="#b01e28"/><path d="M1 3 L7 8 L13 3" fill="none" stroke="#fff" stroke-width="1.1"/></svg>
          roheshkamdar@veltrane.com
        </li>
        <li>
          <svg viewBox="0 0 14 14" aria-hidden="true"><circle cx="7" cy="7" r="6" fill="#b01e28"/><path d="M1 7 H13 M7 1 C4 4 4 10 7 13 M7 1 C10 4 10 10 7 13" fill="none" stroke="#fff" stroke-width="0.9"/></svg>
          www.veltrane.com
        </li>
      </ul>
    </div>
    <div class="accent-line"></div>
    <div class="address-band">4180 Lindqvist Ave, Tampa, FL 33482</div>
  </section>

  <section class="card card-back">
    <div class="brand-name">Veltrane<br>Group</div>
  </section>
</body>
</html>
```